KRTB

We want to design our company brochure. We are a newly established ship management company in Singapore. We manage a fleet of bulk carrier and car carriers. Our job is to run the ships economically and efficiently on behalf of owners of the vessel.
Updates

Project Deadline Extended
Reason: We are not satisfied by the designs as yet. Hence, we are extending the deadline further by 7 days.

Project Deadline Extended
Reason: No designs are up to our expectations

Project Deadline Extended

Target Market(s)

Our target market is various ship owners based all over the world especially in Japan and Europe. These ship owners are looking for third party managers to run their ships economically and efficiently.

Industry/Entity Type

It Company

Colors
32b7a4
33a6d7
00a88f
3276b5
0692cd
86cae6
86cfc6
ebf7f9
edf2f7

Requirements
Must have
• The brochure must have four pages (in form of a folder) with static information, photographs etc with a pocket designed inside to keep printed sheets containing dynamic information.
Write up on our company is attached herewith and also some photographs depicting our ships, crew and the training center.
Information for dynamic sheets is attached in a separate sheets.

```html
<!DOCTYPE html>
<html lang="en">
<head>
<meta charset="utf-8">
<title>KRTB – Company Brochure Spread</title>
<link rel="stylesheet" href="https://fonts.googleapis.com/css2?family=Open+Sans:wght@400;600;700;800&display=swap">
<style>
  :root{
    --blue-deep:#1d5fa6;
    --blue:#3276b5;
    --blue-bright:#0692cd;
    --blue-soft:#86cae6;
    --green:#32b7a4;
    --paper:#f4f6f9;
    --paper-shade:#e6eaf0;
    --ink:#3a3f46;
    --ink-blue:#1f4f97;
    --backdrop:#e9eaec;
  }
  *{box-sizing:border-box;margin:0;padding:0}
  html,body{width:1200px;height:1000px;overflow:hidden}
  body{
    background:radial-gradient(ellipse at 50% 40%,#fafafa 0%,var(--backdrop) 70%,#d9dadc 100%);
    font-family:"Open Sans",Arial,sans-serif;
    position:relative;
  }
  .spread{
    position:absolute;left:40px;top:130px;width:1120px;height:740px;
    display:flex;box-shadow:0 14px 40px rgba(0,0,0,.22);
  }
  .page{position:relative;width:560px;height:740px;overflow:hidden}

  /* left page */
  .page--about{
    background:var(--blue);
    border-bottom:4px solid var(--green);
    border-left:4px solid var(--green);
  }
  .page--about .sheet{
    position:absolute;left:14px;top:20px;right:0;bottom:14px;
    background:linear-gradient(90deg,var(--paper) 0%,#fff 55%,var(--paper-shade) 100%);
  }
  .about-title{
    position:absolute;left:16px;top:14px;
    color:var(--blue-deep);font-weight:800;font-size:22px;letter-spacing:.5px;
  }
  .about-copy{
    position:absolute;left:16px;top:44px;width:312px;
    font-size:9.2px;line-height:12.1px;color:var(--ink);text-align:justify;
  }
  .about-copy p{margin-bottom:12px}
  .photo-column{
    position:absolute;left:340px;top:10px;width:188px;
    display:flex;flex-direction:column;gap:10px;
  }
  .photo{display:block;border:3px solid #fff;box-shadow:0 1px 3px rgba(0,0,0,.25)}
  .photo--carrier{height:108px;background:linear-gradient(180deg,#c7dbe9 0%,#e8eef2 55%,#7c97ab 100%)}
  .photo--suits{height:118px;background:linear-gradient(180deg,#e6e6e4 0%,#d85a3c 55%,#c9c9c6 100%)}
  .photo--bulker{height:118px;background:linear-gradient(180deg,#b8c9d6 0%,#9aa7b0 50%,#6d5a56 100%)}
  .photo--crew{height:120px;background:linear-gradient(180deg,#7e8a8e 0%,#c9b45a 50%,#a7aaa8 100%)}
  .photo--hull{height:118px;background:linear-gradient(180deg,#d7dde3 0%,#8c5d4f 60%,#b4b8bb 100%)}

  /* right page */
  .page--strengths{background:linear-gradient(90deg,var(--paper-shade) 0%,#fff 40%,var(--paper) 100%)}
  .top-band{position:absolute;left:0;top:0;width:100%;height:22px;background:var(--blue)}
  .photo--corridor{
    position:absolute;left:26px;top:36px;width:510px;height:190px;
    background:linear-gradient(90deg,#e9ecef 0%,#d8d1c6 40%,#8a6a4c 55%,#e6e6e6 75%,#c0c3c6 100%);
  }
  .section-tab{
    position:absolute;left:40px;top:246px;height:26px;padding:0 40px 0 18px;
    background:var(--blue);color:#fff;font-size:14px;font-weight:600;letter-spacing:.4px;
    line-height:26px;clip-path:polygon(0 0,100% 0,88% 100%,0 100%);
  }
  .tab-rule{position:absolute;left:40px;top:272px;width:490px;height:2px;background:var(--blue)}
  .strengths-copy{
    position:absolute;left:40px;top:286px;width:490px;
    color:var(--ink-blue);font-weight:700;font-size:12.6px;line-height:17px;text-align:justify;
  }
  .strengths-copy p{margin-bottom:12px}
  .commitment-panel{
    position:absolute;left:0;top:470px;width:100%;height:270px;
    background:linear-gradient(180deg,var(--blue) 0%,var(--blue-deep) 100%);
    border-top-left-radius:70px;
  }
  .commitment-title{
    position:absolute;left:32px;top:34px;color:#fff;font-weight:700;font-size:21px;letter-spacing:.5px;
  }
  .commitment-copy{
    position:absolute;left:32px;top:68px;width:268px;
    color:#e6f1fa;font-size:11.6px;line-height:16px;text-align:justify;
  }
  .photo--berth{
    position:absolute;left:312px;top:26px;width:224px;height:170px;border:3px solid #fff;
    background:linear-gradient(180deg,#bcd3e6 0%,#dfe7ee 40%,#2d2f33 62%,#a9463a 78%,#b9b6b0 100%);
  }
</style>
</head>
<body>
  <main class="spread">
    <section class="page page--about">
      <div class="sheet">
        <h1 class="about-title">ABOUT US</h1>
        <div class="about-copy">
          <p>Keelridge Marine Services Pte. Ltd was established in Singapore in January 2012 as a ship management company to provide Quality service to like-minded ship owners and operators. The objective of the organization has been clear right from the beginning to concentrate on quality rather than quantity. The company has grown quite rapidly with this philosophy in the last 2 years from having 1 ship in April 2012 to 19 ships with full technical management at the end of 2013. KRTB is at the moment managing more than 1 million DWT tonnage, has 16 modern bulk carriers (52,000 DWT, 58,000 DWT, 82,000 DWT and 98,000 DWT) and 3 Car Carriers under their management with at least 4 more ships expected to join by the middle of this year. Apart from managing ships for Harada Kaiun Co., Ltd. Japan who are partners in KRTB, the company has started to move into 3rd party Ship management activities and has bagged a few ships from other Singapore based Owners already. The credit for this growth goes to the strong team work, young and dedicated professionals and commitment that has been the hall mark of the organization. The timing for starting this organization could not have been worse, with the Owners dealing with recession but KRTB saw this as an opportunity to try and find innovative solutions to reduce the Operating expenses for the owners, having Zero downtime and off-hire policy and giving reliable service to the customer's customer. There has been an all-round transparency in the company's approach to safe and smooth operation making them a reliable and trust worthy partners for their clients and owners.</p>
          <p>KRTB has a very different approach towards the ship management activity that they have been involved in. Our philosophy is that the ships are best managed by the officers and crew onboard with the management companies being only in supportive role. We consider ourselves to be primarily in "man-management" business with the real ship managers being onboard the ships. Therefore, our entire focus is towards managing our assets – our sea farers well, supporting them when they need, guiding them when they falter and facilitating resources when they fall short to help them in operating the ships well. The company's Safety Management system is also based on the same approach. We trust and respect our seafarers. Mutual trust and mutual respect has been the basis of our relationship. Compassion and humane approach comes naturally to us – in the recent crisis in Philippines due to the Yolanda super typhoon destruction, all the office employees of KRTB gave their 1 day wages to support the needy crew members and their families.</p>
          <p>Singapore has been developing as a global hub of all shipping activities and therefore, it was quite natural for us to start the company here in Singapore rather than anywhere else. There were no doubt some disadvantages of starting up in Singapore when we did – rising costs, stricter immigration rules to employ expats, etc. however, the advantages of excellent corporate governance, friendly rules and regulations, connectivity etc. easily outweighed the disadvantages. The company is now headquartered in Central business district of Singapore and mitigated the cost disadvantage by opening a support office in Delhi, India and another office in Philippines where we also have a training center now.</p>
        </div>
        <div class="photo-column">
          <div class="photo photo--carrier" role="img" aria-label="Photo of a car carrier vessel at sea"></div>
          <div class="photo photo--suits" role="img" aria-label="Photo of survival suits hanging in a ship locker"></div>
          <div class="photo photo--bulker" role="img" aria-label="Photo of a bulk carrier at anchor"></div>
          <div class="photo photo--crew" role="img" aria-label="Photo of crew in safety gear on a car deck"></div>
          <div class="photo photo--hull" role="img" aria-label="Photo of a ship hull in dry dock"></div>
        </div>
      </div>
    </section>

    <section class="page page--strengths">
      <div class="top-band"></div>
      <div class="photo--corridor" role="img" aria-label="Photo of the company office corridor with name sign"></div>
      <h2 class="section-tab">OUR STRENGTHS</h2>
      <div class="tab-rule"></div>
      <div class="strengths-copy">
        <p>The company derives its strength from its highly skilled professionals who are among the best in the industry and share a common zeal to maintain uncompromised standards of safety, quality and efficiency.</p>
        <p>Honesty, trust, integrity and diligence are some of the qualities which are core to the principles of the company. Such traditional values and an in-depth knowledge of modern marine technologies blends here to produce a unique company that is focused in developing and sustaining prosperous partnerships with ship owners, office members, ship-staff and marine support service companies.</p>
      </div>
      <div class="commitment-panel">
        <h2 class="commitment-title">COMMITMENT</h2>
        <p class="commitment-copy">The company believes that good training, motivation and emphasis on human values are essential for long term success. Consequently, the company is committed to providing an ideal working environment both in its offices and on ships.</p>
        <div class="photo--berth" role="img" aria-label="Photo of a bulk carrier moored at a port berth with cranes"></div>
      </div>
    </section>
  </main>
</body>
</html>
```